Upmarket Dessert Lounge needs a Business Card Design

We are an upmarket dessert lounge needing a business card to match our image.

We want something that is simple yet beautiful, feminine, classy, sophisticated and elegant. We want it to stand out and don't mind if it is bold.

The design should include our logo and colours of red or maroon with gold highlights. We don't mind if black is used.

Marlow & Quince

Target Market(s)

For those who like to indulge or treat themselves and give in to their temptations on good quality desserts.

Industry/Entity Type

Business

Requirements
Must have
• Must include our logo and our name

Marlow & Quince

M & Q

```html
<!DOCTYPE html>
<html lang="en">
<head>
<meta charset="utf-8">
<title>Marlow &amp; Quince — Business Card</title>
<link rel="stylesheet" href="https://fonts.googleapis.com/css2?family=Tinos:wght@400;700&display=swap">
<style>
  :root {
    --maroon: #7a1a1a;
    --peach: #fdd39a;
    --card: #ffffff;
    --ink: #3a3a3a;
    --backdrop: #ece8e3;
    --shadow: rgba(0, 0, 0, 0.28);
  }
  * { box-sizing: border-box; margin: 0; padding: 0; }
  html, body { width: 1200px; height: 417px; overflow: hidden; }
  body {
    background: var(--backdrop);
    font-family: "Tinos", "Times New Roman", serif;
    position: relative;
  }
  .card {
    position: absolute;
    top: 61px;
    width: 515px;
    height: 294px;
    background: var(--card);
    box-shadow: 0 3px 8px var(--shadow);
    overflow: hidden;
  }
  .card--front { left: 54px; }
  .card--back { left: 629px; }
  .edge-band {
    position: absolute;
    left: 0; top: 0;
    width: 12px; height: 100%;
    background: var(--peach);
  }
  .edge-band::before {
    content: "";
    position: absolute;
    left: 0; top: 0;
    width: 100%; height: 150px;
    background: var(--maroon);
  }
  .brand-name {
    position: absolute;
    color: var(--maroon);
    font-weight: 400;
    font-size: 26px;
    letter-spacing: 0.5px;
    white-space: nowrap;
    transform: translate(-50%, -50%);
  }
  .card--front .brand-name { left: 160px; top: 152px; }
  .card--back .brand-name { left: 263px; top: 133px; font-size: 27px; }
  .contact {
    position: absolute;
    left: 358px;
    top: 90px;
    color: var(--ink);
  }
  .contact__name {
    color: var(--maroon);
    font-weight: 700;
    font-size: 17px;
    letter-spacing: 0.3px;
  }
  .contact__title { font-size: 13px; margin-top: 2px; }
  .contact__address { font-size: 13px; line-height: 17px; margin-top: 17px; }
  .contact__list { list-style: none; margin-top: 15px; font-size: 13px; }
  .contact__list li {
    display: flex;
    align-items: center;
    height: 20px;
  }
  .contact__list svg { width: 9px; height: 9px; margin-right: 6px; fill: var(--maroon); }
  .web-address {
    position: absolute;
    left: 0; right: 0;
    top: 256px;
    text-align: center;
    font-size: 13px;
    letter-spacing: 2.6px;
    color: #111;
  }
</style>
</head>
<body>
  <section class="card card--front">
    <div class="edge-band"></div>
    <div class="brand-name">MARLOW &amp; QUINCE</div>
    <div class="contact">
      <p class="contact__name">YOUR NAME</p>
      <p class="contact__title">Title</p>
      <p class="contact__address">00, Complex name<br>City, State 000 000</p>
      <ul class="contact__list">
        <li>
          <svg viewBox="0 0 10 10" aria-hidden="true"><circle cx="5" cy="5" r="5"/><path d="M3 2.5h1.2l.6 1.5-.8.6a4 4 0 0 0 1.4 1.4l.6-.8 1.5.6V7a.8.8 0 0 1-.9.7A4.5 4.5 0 0 1 2.3 3.4.8.8 0 0 1 3 2.5z" fill="#fff"/></svg>
          +1 555 014 2290
        </li>
        <li>
          <svg viewBox="0 0 10 10" aria-hidden="true"><rect x="2.5" y="0" width="5" height="10" rx="1"/><rect x="3.4" y="1.3" width="3.2" height="4.5" fill="#fff"/></svg>
          +1 555 014 2290
        </li>
        <li>
          <svg viewBox="0 0 10 10" aria-hidden="true"><rect x="0" y="2" width="10" height="6.5"/><path d="M0 2l5 3.6L10 2" fill="none" stroke="#fff" stroke-width="0.9"/></svg>
          hello@marlowquince.com
        </li>
        <li>
          <svg viewBox="0 0 10 10" aria-hidden="true"><circle cx="5" cy="5" r="5"/><path d="M0 5h10M5 0v10M1.5 2.5h7M1.5 7.5h7" stroke="#fff" stroke-width="0.7" fill="none"/></svg>
          www.marlowquince.com
        </li>
      </ul>
    </div>
  </section>

  <section class="card card--back">
    <div class="edge-band"></div>
    <div class="brand-name">MARLOW &amp; QUINCE</div>
    <p class="web-address">www.marlowquince.com</p>
  </section>
</body>
</html>
```